Kestrelway Financial Plans

I am looking for a complete resdesign of my small financial presentation. This is a Word Doc/PDF that I print off when meeting with people in private. I often present my "two pager" that I have been using for years and years. It tells them the basics of what I do, how I help people and foundational financial principles.

I have recently gone out on my own in business and have completely rebranded. This presentation is my most used tool, so it is the first of many things I would like to redo. I am hoping it will somehow coordinate with the colors of my business, not necessarily the EXACT same 3 colors everywhere, but have the design colors compliment.

I've uploaded all my logo designs, as well as the current "two-pager". I am not against it going to 3 pages if needed. As it will still land on 2 pages with duplex printing.

It has always been VERY simple. I am wanting it built into a more professional and design specific format, to show off my branding, without being over cluttered.

I am completely open to ANY graphics changes. Obviously some are very novice, the house on the last page has always been overly simplified.

```html
<!DOCTYPE html>
<html lang="en">
<head>
<meta charset="utf-8">
<title>Kestrelway Financial Plans — Two Pager</title>
<link rel="stylesheet" href="https://fonts.googleapis.com/css2?family=Roboto:wght@400;500;700;900&display=swap">
<style>
  :root{
    --backdrop:#77807a;
    --green:#1fa64a;
    --green-soft:#eef7f0;
    --navy:#0c2236;
    --ink:#1b1f24;
    --slate:#7e858b;
    --muted:#555b60;
    --rule:#c9cdd1;
    --forest:#173d31;
    --forest-deep:#0e2620;
    --white:#ffffff;
  }
  *{box-sizing:border-box;margin:0;padding:0}
  html,body{width:1200px;height:1008px;overflow:hidden;background:var(--backdrop)}
  body{font-family:"Roboto",Arial,sans-serif;color:var(--ink)}
  .canvas{position:relative;width:1200px;height:1008px;overflow:hidden;background:var(--backdrop)}
  .abs{position:absolute}

  /* ---------- page one ---------- */
  .page-one{position:absolute;left:49px;top:96px;width:538px;height:740px;background:var(--white);overflow:hidden}
  .brand{position:absolute;left:0;right:0;top:30px;text-align:center}
  .brand-name{font-weight:900;font-size:26px;letter-spacing:1px;color:var(--navy);text-transform:uppercase}
  .brand-sub{display:flex;align-items:center;justify-content:center;gap:10px;margin-top:4px;font-weight:700;font-size:11px;letter-spacing:3px;color:var(--navy)}
  .brand-sub::before,.brand-sub::after{content:"";width:30px;height:2px;background:var(--navy)}
  .banner{position:absolute;background:var(--green);color:var(--white);font-weight:900;text-align:center;text-transform:uppercase}
  .banner-challenge{left:49px;top:97px;width:440px;height:57px;font-size:21px;line-height:57px}
  .challenge-grid{position:absolute;left:35px;top:154px;width:467px;height:231px;border:1px solid #6f8fb0;display:grid;grid-template-columns:1fr 1fr 1fr}
  .challenge-col{position:relative;border-right:1px solid #6f8fb0}
  .challenge-col:last-child{border-right:none}
  .challenge-col.debt{background:var(--green-soft)}
  .col-title{position:absolute;left:14px;top:17px;font-weight:900;font-size:12.5px}
  .stat{position:absolute;left:14px;right:8px;display:flex;gap:7px;align-items:flex-start}
  .stat-ring{flex:none;width:21px;height:21px;border-radius:50%;border:2px solid var(--green);font-size:6.2px;font-weight:700;display:flex;align-items:center;justify-content:center;color:var(--ink)}
  .stat-mark{flex:none;width:21px;height:21px;border-radius:50%;border:3px solid #5f676d;border-right-color:var(--green)}
  .stat-text{font-size:5.6px;line-height:8.8px;text-transform:uppercase;color:var(--ink);padding-top:1px;text-align:justify}
  .source{position:absolute;left:38px;font-size:5.8px;line-height:8.8px;font-weight:700;color:var(--green);text-transform:uppercase}

  .band-facing{position:absolute;left:103px;top:385px;width:333px;height:36px;background:var(--slate);color:var(--white);font-weight:900;font-size:14px;line-height:36px;text-align:center;text-transform:uppercase}
  .step{position:absolute;width:80px;margin-left:-40px;text-align:center}
  .step-icon{width:34px;height:34px;margin:0 auto;border-radius:50%;border:2px solid #8d9398;display:flex;align-items:center;justify-content:center}
  .step-icon span{width:26px;height:26px;border-radius:50%;border:1.5px solid var(--green);display:flex;align-items:center;justify-content:center;font-size:11px;font-weight:700;color:var(--green)}
  .step-label{margin-top:13px;font-size:7px;line-height:10px;font-weight:500;text-transform:uppercase}
  .step-note{position:absolute;font-size:6.6px;line-height:9px;color:var(--muted);text-align:center}
  .flow-tag{position:absolute;left:102px;top:442px;font-size:5.4px;color:var(--muted)}

  .banner-how{left:151px;top:570px;width:236px;height:26px;font-size:14px;line-height:26px;z-index:2}
  .how-panel{position:absolute;left:0;top:0;width:538px;height:740px}
  .pie-label{position:absolute;color:var(--white);font-size:7px;line-height:9px;text-align:center;font-weight:500}
  .savings-tag{position:absolute;left:178px;top:631px;font-size:6.6px;color:var(--green);font-weight:500}
  .goal-list{position:absolute;left:216px;top:626px;list-style:none}
  .goal-list li{height:24.6px;display:flex;align-items:center;gap:6px;color:var(--white);font-size:6.8px;text-transform:uppercase}
  .goal-list li::before{content:"";width:6px;height:6px;background:var(--white)}
  .partners{position:absolute;left:358px;top:610px;display:grid;grid-template-columns:60px 63px;gap:3.6px 3px}
  .partner-badge{height:21px;border-radius:6px;background:#e9eef7;border:1px solid #b9c6dc}
  .page-num{position:absolute;font-size:6.8px;font-weight:700}

  /* ---------- page two ---------- */
  .page-two{position:absolute;left:614px;top:172px;width:537px;height:740px;overflow:hidden;background:linear-gradient(180deg,#eef0f1 0%,#f8f9f9 40%,#e7eaea 70%,#f4f5f5 100%)}
  .banner-rule{left:181px;top:0;width:176px;height:38px;font-size:22px;line-height:40px}
  .plan-head{position:absolute;top:56px;height:29px;display:flex;align-items:center;justify-content:center;text-align:center;color:var(--white);font-weight:700;font-size:8.3px;line-height:10px;text-transform:uppercase}
  .plan-head.dark{background:#000}
  .plan-head.lit{background:var(--green)}
  .rule-table{position:absolute;top:98px;width:123px;border-collapse:collapse;font-size:8.8px}
  .rule-table th{background:var(--navy);color:var(--white);height:26px;font-weight:700;font-size:8.3px}
  .rule-table th:first-child{text-align:left;padding-left:16px}
  .rule-table th:last-child{text-align:right;padding-right:12px}
  .rule-table td{height:26.6px;border:1px solid var(--rule);background:rgba(255,255,255,.55)}
  .rule-table td:first-child{width:60px;padding-left:16px}
  .rule-table td:last-child{text-align:right;padding-right:8px}
  .doubles{position:absolute;top:340px;display:flex;align-items:center;gap:7px;font-weight:700;font-size:9.4px;line-height:12.5px;color:#5b6166;text-transform:uppercase}
  .doubles i{width:22px;height:22px;border-radius:50%;border:3px solid #707880;border-right-color:var(--green);flex:none}
  .structure-field{position:absolute;left:0;top:0}
  .banner-structure{left:150px;top:411px;width:237px;height:52px;font-size:29px;line-height:54px}
  .vehicle{position:absolute;top:508px;color:var(--white)}
  .vehicle h3{font-size:11.2px;font-weight:500;text-transform:uppercase;margin-bottom:10px}
  .vehicle ul{list-style:none}
  .vehicle li{position:relative;padding-left:13px;font-size:9.4px;line-height:13px;margin-bottom:9.3px;color:#eef2f0}
  .vehicle li::before{content:"";position:absolute;left:0;top:4px;width:4px;height:4px;border-radius:50%;background:var(--green)}
  .tax-line{position:absolute;top:627px;color:var(--white);font-weight:700;font-size:14.5px}
  .divider{position:absolute;top:502px;width:1px;height:154px;background:rgba(255,255,255,.18)}
</style>
</head>
<body>
<div class="canvas">

  <!-- PAGE ONE -->
  <section class="page-one" aria-label="Page one: the financial challenge">
    <header class="brand">
      <div class="brand-name">Kestrelway</div>
      <div class="brand-sub">FINANCIAL PLANS</div>
    </header>

    <h1 class="banner banner-challenge">The Financial Challenge</h1>

    <div class="challenge-grid">
      <div class="challenge-col savings">
        <h2 class="col-title">SAVINGS</h2>
        <div class="stat" style="top:46px"><span class="stat-ring">49%</span><p class="stat-text">Canadian employees are living paycheque to paycheque.</p></div>
        <div class="stat" style="top:75px"><span class="stat-ring">25%</span><p class="stat-text">Canadians are unable to cover an unexpected $500 expense</p></div>
        <p class="source" style="top:99px;left:38px">- Northstat Survey (Feb 2023)</p>
        <div class="stat" style="top:115px"><span class="stat-ring">25%</span><p class="stat-text">Canadians need to access their retirement savings early.</p></div>
        <div class="stat" style="top:143px"><span class="stat-ring">20%</span><p class="stat-text" style="padding-top:6px">Canadians have no savings.</p></div>
        <div class="stat" style="top:170px"><span class="stat-ring">39%</span><p class="stat-text">Canadians aged 55-65 have less than $5,000 in savings.</p></div>
        <p class="source" style="top:197px">-Civic Savings Bureau<br>(June 2023)</p>
      </div>

      <div class="challenge-col debt">
        <h2 class="col-title">DEBT</h2>
        <div class="stat" style="top:46px"><span class="stat-mark"></span><p class="stat-text">The average Canadian has $22,131 in consumer debt. Which excludes mortgages</p></div>
        <p class="source" style="top:77px">- Ledgerline (Aug 2024)</p>
        <div class="stat" style="top:94px"><span class="stat-mark"></span><p class="stat-text">Over 55% of Canadians hold credit card debt and the total Canadian household debt has increased to $2.52trillion, including consumer credit, mortgage and non-mortgage loans.</p></div>
        <p class="source" style="top:161px">- Maple Lenders Assoc.<br>(Aug 2024)</p>
      </div>

      <div class="challenge-col insurance">
        <h2 class="col-title">INSURANCE</h2>
        <div class="stat" style="top:46px"><span class="stat-ring">45%</span><p class="stat-text">Canadians do not have individual life insurance coverage,</p></div>
        <div class="stat" style="top:75px"><span class="stat-ring">48%</span><p class="stat-text">Say their families would face financial trouble within 6 months of losing someone</p></div>
        <p class="source" style="top:103px;left:36px">-Lifeward Intl. (Apr 2023)</p>
        <div class="stat" style="top:117px"><span class="stat-mark"></span><p class="stat-text">2-in-5 Canadians (43% women / 44% men) will be diagosed with a form of cancer or other critical illness during their lifetime. every 7 seconds</p></div>
        <p class="source" style="top:166px;left:38px">-Wellnote Data<br>(June 2024)</p>
      </div>
    </div>

    <h2 class="band-facing">Facing the Challenge</h2>

    <span class="flow-tag">$400/$600</span>
    <svg class="abs" style="left:94px;top:448px" width="45" height="8" aria-hidden="true">
      <line x1="0" y1="4" x2="38" y2="4" stroke="#555" stroke-width="1" stroke-dasharray="1.5 1.5"/>
      <path d="M36 1 L43 4 L36 7 Z" fill="#555"/>
    </svg>

    <div class="step" style="left:75px;top:435px"><div class="step-icon"><span>$</span></div><p class="step-label">Cash Flow</p></div>
    <div class="step" style="left:153px;top:435px"><div class="step-icon"><span>$</span></div><p class="step-label">Cash Flow<br>Protection</p></div>
    <div class="step" style="left:231px;top:435px"><div class="step-icon"><span>%</span></div><p class="step-label">Debt<br>Management</p></div>
    <div class="step" style="left:309px;top:435px"><div class="step-icon"><span>⊕</span></div><p class="step-label">Emergency<br>Fund</p></div>
    <div class="step" style="left:387px;top:435px"><div class="step-icon"><span>↑</span></div><p class="step-label">Build Wealth</p></div>
    <div class="step" style="left:465px;top:435px"><div class="step-icon"><span>∞</span></div><p class="step-label">Preserve</p></div>

    <p class="step-note" style="left:50px;top:515px;text-align:left;line-height:14px">Analyze<br>Free Up</p>
    <p class="step-note" style="left:115px;top:515px;width:76px">Income protection</p>
    <svg class="abs" style="left:112px;top:526px" width="80" height="14" aria-hidden="true">
      <line x1="10" y1="1" x2="30" y2="12" stroke="#777" stroke-width=".7"/>
      <line x1="68" y1="1" x2="52" y2="12" stroke="#777" stroke-width=".7"/>
    </svg>
    <p class="step-note" style="left:111px;top:539px;width:36px">Life<br>Insurance</p>
    <p class="step-note" style="left:146px;top:539px;width:36px">CI/DI<br>Insurance</p>
    <p class="step-note" style="left:210px;top:515px;width:34px">20%<br>↓<br>6%-7%</p>
    <p class="step-note" style="left:292px;top:515px;width:34px">20%<br>↓<br>3-6<br>Months</p>
    <p class="step-note" style="left:345px;top:515px;width:86px">Financial Independance Number (F.I.N)</p>
    <svg class="abs" style="left:381px;top:538px" width="16" height="14" aria-hidden="true">
      <rect x="1" y="4" width="14" height="9" rx="1" fill="#555"/><rect x="3" y="1" width="10" height="4" rx="1" fill="none" stroke="#555"/>
    </svg>
    <p class="step-note" style="left:448px;top:515px;width:38px">Leaving a Legacy</p>
    <p class="step-note" style="left:447px;top:541px;width:40px">Will Prep</p>

    <svg class="how-panel" viewBox="0 0 538 740" aria-hidden="true">
      <defs>
        <radialGradient id="howGlow" cx="0.5" cy="0.1" r="0.6">
          <stop offset="0" stop-color="#14453f"/>
          <stop offset="1" stop-color="#0c2236"/>
        </radialGradient>
      </defs>
      <path d="M0 612 Q269 584 538 612 V740 H0 Z" fill="url(#howGlow)"/>
      <circle cx="117" cy="671" r="51" fill="none" stroke="#8c9398" stroke-width="3"/>
      <line x1="117" y1="620" x2="117" y2="722" stroke="var(--green)" stroke-width="2.5"/>
      <line x1="117" y1="671" x2="168" y2="671" stroke="var(--green)" stroke-width="2.5"/>
      <line x1="130" y1="668" x2="182" y2="645" stroke="#8c9398" stroke-width=".5"/>
      <line x1="130" y1="674" x2="195" y2="685" stroke="#8c9398" stroke-width=".5"/>
      <line x1="172" y1="671" x2="202" y2="671" stroke="#fff" stroke-width="1" stroke-dasharray="1.5 1.5"/>
      <path d="M200 668 L206 671 L200 674 Z" fill="#fff"/>
      <line x1="310" y1="671" x2="343" y2="671" stroke="#fff" stroke-width="1" stroke-dasharray="1.5 1.5"/>
      <path d="M342 668 L349 671 L342 674 Z" fill="#fff"/>
    </svg>
    <h2 class="banner banner-how">How Will We Do It</h2>
    <p class="pie-label" style="left:70px;top:661px">LIVING<br>EXPENSES</p>
    <p class="pie-label" style="left:129px;top:646px">TAXES</p>
    <p class="pie-label" style="left:129px;top:682px">DEBT</p>
    <span class="savings-tag">SAVINGS</span>
    <ul class="goal-list">
      <li>Retirement Savings</li>
      <li>Children's Education</li>
      <li>Proper Protection</li>
      <li>Freedom from Debt</li>
    </ul>
    <div class="partners" aria-label="Insurance carrier partners">
      <span class="partner-badge"></span><span class="partner-badge"></span>
      <span class="partner-badge"></span><span class="partner-badge"></span>
      <span class="partner-badge"></span><span class="partner-badge"></span>
      <span class="partner-badge"></span><span class="partner-badge"></span>
      <span class="partner-badge"></span><span class="partner-badge"></span>
    </div>
    <span class="page-num" style="left:503px;top:720px;color:var(--white)">Page 01</span>
  </section>

  <!-- PAGE TWO -->
  <section class="page-two" aria-label="Page two: rule of 72 and structure">
    <h2 class="banner banner-rule">Rule of 72</h2>

    <div class="plan-head dark" style="left:19px;width:123px">Emergency</div>
    <div class="plan-head dark" style="left:145px;width:123px">Opportunity Funding<br>Debt Management</div>
    <div class="plan-head lit" style="left:270px;width:122px">Cashflow Protection</div>
    <div class="plan-head lit" style="left:394px;width:124px">(Life Ins/CI/DI) Cashflow</div>

    <table class="rule-table" style="left:19px">
      <tr><th>AGE</th><th>4%</th></tr>
      <tr><td>29</td><td>$10,000</td></tr>
      <tr><td>47</td><td>$20,000</td></tr>
      <tr><td>65</td><td>$40,000</td></tr>
    </table>
    <table class="rule-table" style="left:145px">
      <tr><th>AGE</th><th>6%</th></tr>
      <tr><td>29</td><td>$10,000</td></tr>
      <tr><td>41</td><td>$20,000</td></tr>
      <tr><td>53</td><td>$40,000</td></tr>
      <tr><td>65</td><td>$80,000</td></tr>
    </table>
    <table class="rule-table" style="left:270px">
      <tr><th>AGE</th><th>8%</th></tr>
      <tr><td>29</td><td>$10,000</td></tr>
      <tr><td>38</td><td>$20,000</td></tr>
      <tr><td>47</td><td>$40,000</td></tr>
      <tr><td>56</td><td>$80,000</td></tr>
      <tr><td>65</td><td>$160,000</td></tr>
    </table>
    <table class="rule-table" style="left:395px">
      <tr><th>AGE</th><th>8%</th></tr>
      <tr><td>29</td><td>$10,000</td></tr>
      <tr><td>35</td><td>$20,000</td></tr>
      <tr><td>41</td><td>$40,000</td></tr>
      <tr><td>47</td><td>$80,000</td></tr>
      <tr><td>53</td><td>$160,000</td></tr>
      <tr><td>59</td><td>$320,000</td></tr>
      <tr><td>65</td><td>$640,000</td></tr>
    </table>

    <p class="doubles" style="left:22px"><i></i>Money doubles<br>every 18 years</p>
    <p class="doubles" style="left:151px"><i></i>Money doubles<br>every 12 years</p>
    <p class="doubles" style="left:280px"><i></i>Money doubles<br>every 9 years</p>
    <p class="doubles" style="left:409px"><i></i>Money doubles<br>every 6 years</p>

    <svg class="structure-field" width="537" height="740" viewBox="0 0 537 740" aria-hidden="true">
      <defs>
        <linearGradient id="forestFill" x1="0" y1="0" x2="0" y2="1">
          <stop offset="0" stop-color="#2a4d42"/>
          <stop offset=".5" stop-color="var(--forest)"/>
          <stop offset="1" stop-color="var(--forest-deep)"/>
        </linearGradient>
        <radialGradient id="forestGlow" cx="0" cy="0.75" r="0.55">
          <stop offset="0" stop-color="#16a05a" stop-opacity=".75"/>
          <stop offset="1" stop-color="#16a05a" stop-opacity="0"/>
        </radialGradient>
      </defs>
      <path d="M0 520 Q268 350 537 520 V740 H0 Z" fill="url(#forestFill)"/>
      <path d="M0 520 Q268 350 537 520 V740 H0 Z" fill="url(#forestGlow)"/>
      <path d="M0 514 Q268 345 537 514" fill="none" stroke="#ffffff" stroke-opacity=".5" stroke-width="1"/>
    </svg>

    <h2 class="banner banner-structure">Structure</h2>

    <span class="divider" style="left:145px"></span>
    <span class="divider" style="left:259px"></span>
    <span class="divider" style="left:398px"></span>

    <div class="vehicle" style="left:19px;width:118px">
      <h3>Home</h3>
      <ul><li>Partner with mortgage Brokers for Best rates</li><li>Mortgage Insurance alternatives</li></ul>
    </div>
    <div class="vehicle" style="left:167px;width:90px">
      <h3>RRSP</h3>
      <ul><li>Tax Deduction</li><li>Tax Deferred</li></ul>
    </div>
    <div class="vehicle" style="left:273px;width:120px">
      <h3>TFSA</h3>
      <ul><li>No Tax Deductions</li><li>Tax Free Growth</li><li>2009-$95,000</li><li>LIMIT 2023-$7,000/YR</li></ul>
    </div>
    <div class="vehicle" style="left:418px;width:115px">
      <h3>Prem Life</h3>
      <ul><li>No Tax Deductions</li><li>Qualify</li><li>Tax Deffered Growth</li></ul>
    </div>

    <p class="tax-line" style="left:36px">SELL</p>
    <p class="tax-line" style="left:167px">100% TAX</p>
    <p class="tax-line" style="left:273px">0% TAX</p>
    <p class="tax-line" style="left:418px">0% TAX</p>

    <span class="page-num" style="left:500px;top:720px;color:var(--white)">Page 02</span>
  </section>

</div>
</body>
</html>
```